Captivating packaging design for sports company.

We need a packaging design that encompasses our resistance bands workout set. Our focus is quality, convenience, and versatility. The design should be tailored to our broad array of customer across all paths. We would like the packaging to reflect our brand and product features such as: the LBS(weight) listed on each of the bands, convenience for travel and at home, highest quality, for all fitness levels, and free eBook. We'd also like to include a couple of our reviews on the packaging. Please refer to our listing on Varlo for additional information https://www.shopvarlo.com/Brisklane-Athletics-Resistance-Workout-Carrying/dp/K47TR2XMNQ/ref=sr_1_1?ie=UTF8&qid=1470453588&sr=8-1&keywords=brisklane+athletics+resistance+bands
Please reach out with additional questions for any further details. Thank you.
Target Market(s)
Sports, fitness, and health enthusiasts of all ages.
Industry/Entity Type
It Company
Look and feel
Each slider illustrates characteristics of the customer's brand and the style your logo design should communicate.

```html
<!DOCTYPE html>
<html lang="en">
<head>
<meta charset="utf-8">
<title>Brisklane Athletics Resistance Bands Packaging</title>
<link href="https://fonts.googleapis.com/css2?family=Michroma&family=Archivo+Black&display=swap" rel="stylesheet">
<style>
  :root {
    --bg: #bdbdbd;
    --black: #111111;
    --panel-dark: #1a1a1a;
    --top-dark: #232323;
    --top-mid: #3a3835;
    --gold: #c7a26a;
    --tan: #cda272;
    --orange: #f39200;
    --white: #ffffff;
    --photo-light: #f7f7f7;
    --photo-mid: #dcdcdc;
  }
  * { box-sizing: border-box; margin: 0; padding: 0; }
  html, body { width: 1200px; height: 1200px; overflow: hidden; }
  body {
    background: var(--bg);
    font-family: "Michroma", sans-serif;
    position: relative;
  }
  .packaging {
    position: absolute;
    left: 60px; top: 90px;
    width: 1080px; height: 1000px;
  }

  /* Top face */
  .top-panel {
    position: absolute; left: 220px; top: 0;
    width: 860px; height: 220px;
    background: linear-gradient(90deg, var(--top-dark) 0%, var(--top-mid) 50%, var(--top-dark) 100%);
  }

  /* Side panel */
  .side-panel {
    position: absolute; left: 0; top: 220px;
    width: 220px; height: 780px;
    background: var(--panel-dark);
    padding-top: 70px;
  }
  .brand {
    display: flex; align-items: center; gap: 10px;
    color: var(--gold);
    font-family: "Michroma", sans-serif;
    line-height: 1.05;
  }
  .brand-dot { border-radius: 50%; background: var(--gold); flex: none; }
  .side-panel .brand { justify-content: center; font-size: 13px; }
  .side-panel .brand-dot { width: 26px; height: 26px; }

  .box-contents {
    margin: 130px 0 0 26px;
    color: var(--gold);
    font-size: 11px;
    line-height: 1.65;
    list-style: none;
  }
  .box-contents .heading,
  .box-contents .extra { padding-left: 40px; }

  .tagline {
    position: absolute; left: 22px; top: 470px;
    font-size: 42px; line-height: 1.15;
    color: transparent;
    -webkit-text-stroke: 1.5px var(--gold);
    letter-spacing: 1px;
  }
  .resistance-note {
    position: absolute; left: 0; right: 0; bottom: 0;
    height: 128px;
    background: var(--tan);
    display: flex; align-items: center; justify-content: center;
    text-align: center;
    font-size: 13px; line-height: 1.35;
    color: var(--black);
  }

  /* Front panel */
  .front-panel {
    position: absolute; left: 220px; top: 220px;
    width: 860px; height: 780px;
    background: var(--panel-dark);
    overflow: hidden;
  }
  .hero-photo {
    position: absolute; left: 0; top: 0;
    width: 490px; height: 100%;
    background: linear-gradient(180deg, var(--photo-light) 0%, var(--photo-mid) 55%, var(--photo-light) 100%);
  }
  .front-panel .brand {
    position: absolute; left: 540px; top: 140px;
    font-size: 22px;
  }
  .front-panel .brand-dot { width: 44px; height: 44px; }

  .title-banner {
    position: absolute; left: 366px; top: 262px;
    width: 494px; height: 148px;
    background: var(--orange);
    color: var(--white);
    font-family: "Archivo Black", sans-serif;
    padding: 22px 0 0 20px;
    line-height: 0.98;
  }
  .title-banner .kicker { font-size: 21px; letter-spacing: 0.5px; }
  .title-banner .product { font-size: 50px; letter-spacing: 1px; }

  .product-name, .feature-list {
    position: absolute; left: 560px;
    color: var(--gold);
    font-size: 17px; line-height: 1.85;
    list-style: none;
  }
  .product-name { top: 440px; }
  .feature-list { top: 560px; }

  .bonus-badge {
    position: absolute; left: 276px; top: 590px;
    width: 210px; height: 210px;
    border-radius: 50%;
    background: var(--white);
    border: 3px solid var(--orange);
    text-align: center;
    padding-top: 16px;
    color: var(--orange);
  }
  .bonus-badge .label { font-family: "Archivo Black", sans-serif; font-size: 26px; line-height: 1; }
  .bonus-badge .detail {
    font-family: "Archivo Black", sans-serif; font-size: 12px; line-height: 1.2; margin-top: 4px;
  }
  .ebook-cover {
    width: 72px; height: 88px; margin: 8px auto 0;
    background: linear-gradient(180deg, #e9eef2, #a9b7c2);
  }
</style>
</head>
<body>
  <main class="packaging">
    <div class="top-panel"></div>

    <section class="side-panel">
      <div class="brand"><span class="brand-dot"></span><span>BRISKLANE<br>ATHLETICS</span></div>
      <ul class="box-contents">
        <li class="heading">IN THE BOX</li>
        <li>x1 YELLOW - 2-4LBS</li>
        <li>x1 GREEN - 4-6LBS</li>
        <li>x1 BLUE - 10-12LBS</li>
        <li>x1 RED - 15-20LBS</li>
        <li>x1 BLACK - 25-30LBS</li>
        <li class="extra">CARRY CASE</li>
        <li class="extra">E-BOOK</li>
      </ul>
      <p class="tagline">TONE<br>BURN<br>BUILD</p>
      <p class="resistance-note">UP TO 75LBS<br>OF TOTAL<br>RESISTANCE</p>
    </section>

    <section class="front-panel">
      <div class="hero-photo" role="img" aria-label="Photo of an athlete in a sports top and shorts stretching a resistance band with handles, on a white background"></div>
      <div class="brand"><span class="brand-dot"></span><span>BRISKLANE<br>ATHLETICS</span></div>
      <div class="title-banner">
        <div class="kicker">HIGH QUALITY</div>
        <div class="product">RESISTANCE<br>BANDS</div>
      </div>
      <p class="product-name">Brisklane Athletics<br>Resistance Band<br>Workout Set</p>
      <ul class="feature-list">
        <li>4 Colourful Bands</li>
        <li>Door Anchor</li>
        <li>2 Handles</li>
        <li>2 Ankle Straps</li>
        <li>Carrying Case</li>
      </ul>
      <div class="bonus-badge">
        <div class="label">BONUS</div>
        <div class="detail">Product and<br>Workout<br>Guide eBook</div>
        <div class="ebook-cover" role="img" aria-label="Cover of the product and workout guide eBook"></div>
      </div>
    </section>
  </main>
</body>
</html>
```